BRISK requires an exciting new business card

New business card required for BRISK. We are a new market research consultancy and want our brand to be approachable and be contemporary/modern, bold, uncomplicated/simple, and use friendly and easy to read fonts.

A draft website front page is attached to give you a feel (the pictures will be improved over the coming days).

The business card will be printed on 600gsm card, full colour both sides. The card is unique in that it allows one of four colours to be placed within the seam of the card (see http://uk.prentvo.com/products/gilt/business-cards.html)

The logo has been designed in yellow on white, white on yellow, yellow on black and black on yellow - please select whichever you feel most appropriate from the attached document (please use the versions with the tagline). I think my preference is yellow on white for the front, and then yellow or black as the dominant colour on the back.

Telephone numbers will be given next week as they are now being finalised.

Thanks

Target Market(s)

Professionals in large corporates, such as Marketing Managers at Grovane, Fizzaro Pop, Delmarco etc.

Industry/Entity Type

Market Research

Requirements
Must have
• Dana Pruitt QPMR
brisk
Level 4, 37 Quarrell St
Surrey Hills
NSW 2010
Tel: 02 XXXX XXXX
Mob: XXXX XXXXXX
Email: dana@briskqr.com.au
Web: www.briskqr.com.au

```html
<!DOCTYPE html>
<html lang="en">
<head>
<meta charset="utf-8">
<title>BRISK business card</title>
<link rel="stylesheet" href="https://fonts.googleapis.com/css2?family=Source+Sans+3:wght@400;600;700&display=swap">
<style>
  :root {
    --yellow: #fdcb0a;
    --charcoal: #3c3c3c;
    --white: #ffffff;
    --backdrop: #e6e6ea;
    --font: "Source Sans 3", sans-serif;
  }
  * { margin: 0; padding: 0; box-sizing: border-box; }
  html, body { width: 1200px; height: 987px; overflow: hidden; background: var(--backdrop); font-family: var(--font); }
  .canvas { position: relative; width: 1200px; height: 987px; }

  .card {
    position: absolute; left: 300px; width: 600px; height: 343px;
    border-radius: 22px; overflow: hidden;
    box-shadow: 0 6px 18px rgba(0,0,0,0.12);
  }
  .card-front { top: 90px; background: var(--white); }
  .card-back { top: 553px; background: var(--yellow); }
  .card-shapes { position: absolute; inset: 0; }

  .wordmark { position: absolute; font-weight: 700; line-height: 1; letter-spacing: -2px; }
  .card-front .wordmark { left: 250px; top: 62px; font-size: 104px; color: var(--yellow); }
  .wordmark-dot { position: absolute; border-radius: 50%; }
  .card-front .wordmark-dot { left: 488px; top: 110px; width: 30px; height: 30px; background: var(--yellow); }

  .contact { position: absolute; color: var(--charcoal); font-size: 14.5px; line-height: 20px; }
  .contact-person { left: 24px; top: 218px; }
  .contact-name { font-weight: 700; font-size: 16px; }
  .contact-name span { font-weight: 400; }
  .contact-divider { position: absolute; left: 212px; top: 250px; width: 1px; height: 78px; background: var(--charcoal); opacity: 0.6; }
  .contact-lines { left: 224px; top: 250px; list-style: none; }
  .contact-lines li { display: flex; align-items: center; gap: 7px; }
  .contact-lines svg { width: 13px; height: 13px; flex: none; }

  .card-back .wordmark { left: 0; right: 0; top: 92px; text-align: center; font-size: 150px; color: var(--charcoal); padding-right: 40px; }
  .card-back .wordmark-dot { left: 470px; top: 168px; width: 40px; height: 40px; background: var(--charcoal); }
  .back-web { position: absolute; left: 0; right: 0; top: 262px; text-align: center; font-size: 17px; letter-spacing: 5px; color: var(--charcoal); }
</style>
</head>
<body>
<div class="canvas">

  <section class="card card-front">
    <svg class="card-shapes" viewBox="0 0 600 343" aria-hidden="true">
      <path d="M0,40 Q230,300 600,250 L600,343 L0,343 Z" fill="var(--yellow)"/>
      <path d="M0,10 Q220,285 470,262 Q225,268 0,38 Z" fill="var(--charcoal)"/>
    </svg>
    <div class="wordmark">brisk</div>
    <div class="wordmark-dot"></div>

    <div class="contact contact-person">
      <div class="contact-name">Dana Pruitt <span>QPMR</span></div>
      <div>Level 4, 37 Quarrell St</div>
      <div>Kellerton Park, VIC 3190</div>
    </div>
    <div class="contact-divider"></div>
    <ul class="contact contact-lines">
      <li><svg viewBox="0 0 16 16"><circle cx="8" cy="8" r="7.5" fill="var(--charcoal)"/><path d="M5,4 L7,4 L7.5,6.5 L6.5,7.3 Q7.5,9 8.8,9.6 L9.6,8.6 L12,9.2 L12,11 Q8,12 5,8 Q4.4,6 5,4Z" fill="var(--yellow)"/></svg>02 8765 4321</li>
      <li><svg viewBox="0 0 16 16"><rect x="4" y="1" width="8" height="14" rx="1.5" fill="var(--charcoal)"/><rect x="5.5" y="3" width="5" height="6" fill="var(--yellow)"/></svg>0412 345 678</li>
      <li><svg viewBox="0 0 16 16"><rect x="1" y="3.5" width="14" height="9" fill="var(--charcoal)"/><path d="M1.5,4 L8,9 L14.5,4" stroke="var(--yellow)" stroke-width="1.2" fill="none"/></svg>dana@briskqr.com.au</li>
      <li><svg viewBox="0 0 16 16"><circle cx="8" cy="8" r="7" fill="var(--charcoal)"/><g stroke="var(--yellow)" stroke-width="1" fill="none"><ellipse cx="8" cy="8" rx="3" ry="7"/><path d="M1,8 H15 M2.5,4.5 H13.5 M2.5,11.5 H13.5"/></g></svg>www.briskqr.com.au</li>
    </ul>
  </section>

  <section class="card card-back">
    <div class="wordmark">brisk</div>
    <div class="wordmark-dot"></div>
    <div class="back-web">www.briskqr.com.au</div>
  </section>

</div>
</body>
</html>
```